International Clinical Software Company needs a new business card design

We are looking for a new business card design for our company that has recently expanded into the UK market, making us a multinational company.
After having rebranded our website and produced a new style guide, we are looking for a business card that is creative and attention grabbing, while being consistent with the style and colour scheme used on the new website, www.plumvora.example
We produce care management technology for the aged care market, but the main aspect we aim to communicate is the human element of our software, and the way it assists in providing better care for aged people, and stronger relationships between aged people and the staff that care for them.
Our current business card is a dark green with gold text, which makes the text quite difficult to read, not very aesthetically appealing and the colour scheme looks quite dated.
We would like something fresh and modern, that can still be colourful but doesn't use large blocks of dark colour, and uses the colours within our logo.
Something tying in with the leaves that are used in our logo could work quite nicely, along with the Autumn/Fall colours of soft greens, yellows and reds (also in our existing logo). However also happy to look at fresh, completely out of the box ideas we may not have yet considered.
Target Market(s)
The people that receive this business card work in the aged card or health industry and are either corporate/management level staff or clinical (Registered Nurses, care workers etc.)
Industry/Entity Type
Health Product
Contact Information for Business Card
Company Name - BrindlewayCare
Company locations: United Kingdom, Australia, New Zealand
Staff Details:
Staff name: Derek Mallow
Staff job title: Executive Chairman
Staff email: d.mallow@plumvora.example
Office phone number: 01742 918576
Font styles to use
Other font styles liked:
- Calibri
Requirements
Must have
- Must include the BrindlewayCare brand name in it's current font
- Must include logo (3 leaves in gold circle)
- Must include Business Card Details
Nice to have
- Elements of gold
- White space
- Something autumn themed but not too cliched
Should not have
- No blue - used by a major competitor and we would like to differentiate from them
- Large blocks of dark green colour (the green that appears in our leaves on the logo on our current business card is the background colour and it is far too dark)

```html
<!DOCTYPE html>
<html lang="en">
<head>
<meta charset="UTF-8">
<title>BrindlewayCare — Business Card</title>
<link rel="stylesheet" href="https://fonts.googleapis.com/css2?family=Carlito:wght@400;700&display=swap">
<style>
  :root {
    --backdrop: #3a3733;
    --card: #f7f3ea;
    --card-edge: #e2d8c3;
    --gold: #a88d55;
    --gold-line: #bda877;
    --ink: #3a342c;
    --divider: #d9cdb3;
  }
  html, body {
    margin: 0;
    padding: 0;
    width: 1200px;
    height: 900px;
    overflow: hidden;
    background: var(--backdrop);
    font-family: "Carlito", "Calibri", sans-serif;
  }
  .canvas {
    position: relative;
    width: 1200px;
    height: 900px;
  }
  .card {
    position: absolute;
    top: 305px;
    width: 500px;
    height: 290px;
    background: var(--card);
    border: 1px solid var(--card-edge);
    border-radius: 24px;
    box-sizing: border-box;
  }
  .card--details { left: 80px; }
  .card--brand { left: 620px; }

  /* contact side */
  .brand-mark {
    position: absolute;
    left: 34px;
    top: 62px;
    width: 190px;
    display: flex;
    flex-direction: column;
    align-items: center;
    gap: 14px;
  }
  .brand-mark__circle { width: 116px; height: 116px; }
  .brand-mark__name {
    color: var(--gold);
    font-size: 22px;
    font-weight: 400;
    letter-spacing: 0.5px;
  }
  .divider {
    position: absolute;
    left: 250px;
    top: 40px;
    width: 1px;
    height: 210px;
    background: var(--divider);
  }
  .contact {
    position: absolute;
    left: 272px;
    top: 52px;
    color: var(--ink);
    font-size: 14px;
    line-height: 1.35;
  }
  .contact p { margin: 0; }
  .contact__name {
    color: var(--gold);
    font-size: 21px;
    font-weight: 700;
  }
  .contact .contact__title { margin: 2px 0 20px; }
  .contact .contact__locations { margin: 0 0 20px; }
  .contact__line {
    display: flex;
    align-items: center;
    gap: 8px;
  }
  .contact .contact__line + .contact__line { margin-top: 6px; }
  .contact__icon { width: 12px; height: 12px; flex: none; }

  /* brand side */
  .brand-lockup {
    position: absolute;
    inset: 0;
    display: flex;
    flex-direction: column;
    align-items: center;
    justify-content: center;
    gap: 18px;
  }
  .brand-lockup__circle { width: 88px; height: 88px; }
  .brand-lockup__name {
    color: var(--gold);
    font-size: 44px;
    font-weight: 400;
    letter-spacing: 1px;
  }
</style>
</head>
<body>
<main class="canvas">
  <section class="card card--details" aria-label="Business card, contact side">
    <div class="brand-mark">
      <svg class="brand-mark__circle" viewBox="0 0 116 116" aria-hidden="true">
        <circle cx="58" cy="58" r="55" fill="none" stroke="var(--gold-line)" stroke-width="3"/>
      </svg>
      <span class="brand-mark__name">BrindlewayCare</span>
    </div>
    <div class="divider"></div>
    <div class="contact">
      <p class="contact__name">Derek Mallow</p>
      <p class="contact__title">Executive Chairman</p>
      <p class="contact__locations">United Kingdom, Australia<br>New Zealand</p>
      <p class="contact__line">
        <svg class="contact__icon" viewBox="0 0 24 24" aria-hidden="true">
          <path fill="var(--gold)" d="M6.6 10.8a15.1 15.1 0 0 0 6.6 6.6l2.2-2.2a1 1 0 0 1 1-.25 11.4 11.4 0 0 0 3.6.57 1 1 0 0 1 1 1V20a1 1 0 0 1-1 1A17 17 0 0 1 3 4a1 1 0 0 1 1-1h3.5a1 1 0 0 1 1 1c0 1.25.2 2.45.57 3.57a1 1 0 0 1-.25 1z"/>
        </svg>
        01742 918576
      </p>
      <p class="contact__line">
        <svg class="contact__icon" viewBox="0 0 24 24" aria-hidden="true">
          <rect x="2" y="5" width="20" height="14" rx="2" fill="none" stroke="var(--gold)" stroke-width="2"/>
          <path d="M3 6l9 7 9-7" fill="none" stroke="var(--gold)" stroke-width="2"/>
        </svg>
        d.mallow@plumvora.example
      </p>
    </div>
  </section>

  <section class="card card--brand" aria-label="Business card, brand side">
    <div class="brand-lockup">
      <svg class="brand-lockup__circle" viewBox="0 0 88 88" aria-hidden="true">
        <circle cx="44" cy="44" r="41" fill="none" stroke="var(--gold-line)" stroke-width="3"/>
      </svg>
      <span class="brand-lockup__name">BrindlewayCare</span>
    </div>
  </section>
</main>
</body>
</html>
```